Stationery Design Project

I need a stationary design for our company. we are based in Houston, TX and we are called Mira Vell Lending. And we are wanting to brand our MoneyMendPlus program, which includes our tax preparation and restoration, credit repair service. Although our business offers other programs, we are interested in mainly focusing on The MoneyMendPlus program. We are looking for way to brand our ourselves and I believe that a great stationery design will help in achieving this goal. Our logo design is blue and light blue. the slogan is orange.

Industry/Entity Type

Business

Requirements
Must have
• Address: 30871 Calloway Ln. B-22
Houston, TX 75419
Tel. 555-318-6207
Fax 555-294-7153
www.miravelllending.example
info@miravelllending.example
Our Slogan: Confidence, Renewed

```html
<!DOCTYPE html>
<html lang="en">
<head>
<meta charset="utf-8">
<title>Mira Vell Lending – Business Card</title>
<link rel="stylesheet" href="https://fonts.googleapis.com/css2?family=Tinos:wght@400;700&display=swap">
<style>
  :root {
    --navy: #163d66;
    --navy-line: #2a5585;
    --sky: #8fb3d9;
    --paper: #ffffff;
    --ink: #222222;
    --orange: #f39c1f;
    --program-blue: #1e76b3;
    --stage: #e9ecef;
  }
  * { margin: 0; padding: 0; box-sizing: border-box; }
  html, body {
    width: 1200px; height: 394px; overflow: hidden;
    background: var(--stage);
    font-family: "Tinos", "Times New Roman", serif;
  }
  .canvas { position: relative; width: 1200px; height: 394px; }

  /* Front card */
  .card-front {
    position: absolute; left: 35px; top: 37px; width: 546px; height: 315px;
    background: var(--paper);
  }
  .front-band { position: absolute; left: 0; top: 0; width: 77px; height: 100%; background: var(--navy); }
  .front-rule { position: absolute; left: 84px; top: 0; width: 4px; height: 100%; background: var(--navy-line); }
  .brand-tile {
    position: absolute; left: 27px; top: 0; width: 143px; height: 163px;
    background: var(--paper);
  }
  .brand-tile-inner {
    position: absolute; left: 13px; top: 30px; width: 121px; height: 121px;
    background: var(--navy); outline: 2px solid var(--sky); outline-offset: -5px;
    display: flex; align-items: flex-end; justify-content: center;
    padding-bottom: 21px;
  }
  .brand-name { color: #fff; font-size: 11px; text-align: center; line-height: 1.3; }

  .contact-list { position: absolute; left: 95px; top: 169px; list-style: none; }
  .contact-list li {
    display: flex; align-items: center; gap: 6px;
    font-size: 14px; color: var(--ink); height: 22px;
  }
  .contact-list svg { width: 12px; height: 12px; fill: var(--navy); flex: none; }
  .address { position: absolute; left: 95px; top: 268px; font-size: 14px; line-height: 17px; color: var(--ink); }

  .program { position: absolute; left: 350px; top: 235px; width: 180px; text-align: center; }
  .program-name { font-size: 22px; color: var(--program-blue); }
  .program-slogan {
    margin-top: 16px; font-size: 14px; font-weight: 700; color: var(--orange); letter-spacing: 1px;
  }

  /* Back card */
  .card-back {
    position: absolute; left: 612px; top: 43px; width: 549px; height: 314px;
    background: var(--navy);
  }
  .back-brand {
    position: absolute; left: 0; top: 135px; width: 100%; text-align: center;
    color: #fff; font-size: 26px;
  }
  .back-url {
    position: absolute; left: 0; top: 269px; width: 100%; text-align: center;
    color: #fff; font-size: 14px; letter-spacing: 2.5px;
  }
</style>
</head>
<body>
<main class="canvas">

  <section class="card-front" aria-label="Business card front">
    <div class="front-band"></div>
    <div class="front-rule"></div>
    <div class="brand-tile">
      <div class="brand-tile-inner"><p class="brand-name">Mira Vell Lending</p></div>
    </div>

    <ul class="contact-list">
      <li><svg viewBox="0 0 12 12"><path d="M2.5 1l2 2-1 1.5c.8 1.6 2 2.8 3.5 3.5L8.5 7l2 2-1.5 2C5 10.5 1.5 7 1 3z"/></svg>555-318-6207</li>
      <li><svg viewBox="0 0 12 12"><rect x="1" y="5" width="10" height="6" rx="1"/><rect x="3" y="1" width="6" height="4"/></svg>555-294-7153</li>
      <li><svg viewBox="0 0 12 12"><path d="M1 3h10v7H1z M1 3l5 4 5-4" stroke="#fff" stroke-width=".8"/></svg>info@miravelllending.example</li>
      <li><svg viewBox="0 0 12 12"><circle cx="6" cy="6" r="5"/><path d="M1 6h10M6 1c-2.5 3-2.5 7 0 10M6 1c2.5 3 2.5 7 0 10" stroke="#fff" stroke-width=".7" fill="none"/></svg>www.miravelllending.example</li>
    </ul>

    <p class="address">30871 Calloway Ln. B-22<br>Houston, TX 75419</p>

    <div class="program">
      <p class="program-name">MoneyMendPlus</p>
      <p class="program-slogan">Confidence, Renewed</p>
    </div>
  </section>

  <section class="card-back" aria-label="Business card back">
    <p class="back-brand">Mira Vell Lending</p>
    <p class="back-url">www.miravelllending.example</p>
  </section>

</main>
</body>
</html>
```